real esate business card with company logo and name

we need a business card design for a real esate company

The company name is Walsh & Brand Pty Ltd, and we have our logo designed and will upload. We want classic or moden feel. Black or white background. looks more textured. Should include folowinginformations
Owen Walsh and Lucy Brand
Sales Agents & Onsite Manager
p: 07 5948 2063
F: 07 5948 2174
M:0431 857 219
3/42 Marlow Crescent, FERNLEA QLD 4213

We want this business card looks professonal. Thank you in advance.

Industry/Entity Type

Real Estate Agent

Contact Information for Business Card

Owen Walsh and Lucy Brand
Onsite Manager & Sales Agents
p: 07 5948 2063
M:0431 857 219

Font styles to use
Serif

Colors
000000
fbfbfb
333333
959595

Requirements
Must have
• company logo and name, black or white back ground

```html
<!DOCTYPE html>
<html lang="en">
<head>
<meta charset="utf-8">
<title>Walsh &amp; Brand Pty Ltd — Business Card</title>
<link rel="stylesheet" href="https://fonts.googleapis.com/css2?family=Cinzel:wght@400;600&family=Montserrat:wght@500&display=swap">
<style>
  :root {
    --ink: #000000;
    --paper: #fbfbfb;
    --charcoal: #333333;
    --grey: #959595;
    --silver-light: #f1f1f1;
    --silver-mid: #d4d4d4;
    --silver-dark: #b9b9b9;
    --stage: #e6e6e6;
  }
  * { box-sizing: border-box; margin: 0; padding: 0; }
  html, body { width: 1200px; height: 913px; overflow: hidden; }
  body {
    background: var(--stage);
    display: flex;
    flex-direction: column;
    align-items: center;
    justify-content: center;
    gap: 32px;
  }
  .card {
    width: 680px;
    height: 410px;
    position: relative;
    overflow: hidden;
    box-shadow: 0 6px 18px rgba(0,0,0,.18);
  }

  /* Front — textured silver */
  .card--front {
    background:
      repeating-radial-gradient(circle at 30% 40%, rgba(255,255,255,.18) 0 1px, rgba(0,0,0,.04) 2px 3px),
      linear-gradient(120deg, var(--silver-mid) 0%, var(--silver-light) 45%, var(--silver-dark) 100%);
    display: flex;
    align-items: center;
  }
  .brand-block {
    width: 300px;
    display: flex;
    flex-direction: column;
    align-items: center;
    gap: 26px;
  }
  .brand-square {
    width: 92px;
    height: 92px;
    background: var(--grey);
  }
  .brand-name {
    font-family: "Montserrat", sans-serif;
    font-weight: 500;
    font-size: 15px;
    letter-spacing: 2px;
    text-transform: uppercase;
    color: var(--charcoal);
  }
  .divider {
    width: 1px;
    height: 250px;
    background: var(--grey);
  }
  .contact-block {
    padding-left: 28px;
    font-family: "Cinzel", serif;
    color: var(--charcoal);
  }
  .contact-names {
    font-size: 22px;
    font-weight: 400;
    color: var(--charcoal);
    margin-bottom: 4px;
  }
  .contact-role {
    font-size: 12.5px;
    margin-bottom: 18px;
  }
  .contact-address {
    font-size: 13px;
    line-height: 1.45;
    margin-bottom: 16px;
  }
  .contact-list { list-style: none; font-size: 13px; }
  .contact-list li {
    display: flex;
    align-items: center;
    gap: 10px;
    margin-bottom: 6px;
  }
  .contact-list svg { width: 12px; height: 12px; fill: var(--charcoal); }

  /* Back — glossy black */
  .card--back {
    background:
      linear-gradient(115deg, rgba(255,255,255,0) 40%, rgba(255,255,255,.09) 55%, rgba(255,255,255,0) 70%),
      var(--ink);
    display: flex;
    flex-direction: column;
    align-items: center;
    justify-content: center;
    gap: 30px;
  }
  .card--back .brand-square { width: 120px; height: 120px; background: var(--grey); }
  .card--back .brand-name { color: var(--grey); font-size: 19px; letter-spacing: 3px; }
</style>
</head>
<body>
  <section class="card card--front" aria-label="Business card front">
    <div class="brand-block">
      <div class="brand-square"></div>
      <p class="brand-name">Walsh &amp; Brand Pty Ltd</p>
    </div>
    <div class="divider"></div>
    <div class="contact-block">
      <h1 class="contact-names">Owen Walsh &amp; Lucy Brand</h1>
      <p class="contact-role">Sales Agents &amp; Onsite Manager</p>
      <p class="contact-address">3/42 Marlow Crescent<br>FERNLEA QLD 4213</p>
      <ul class="contact-list">
        <li>
          <svg viewBox="0 0 24 24" aria-label="Phone"><path d="M6.6 10.8a15 15 0 0 0 6.6 6.6l2.2-2.2a1 1 0 0 1 1-.25 11.4 11.4 0 0 0 3.6.57 1 1 0 0 1 1 1V20a1 1 0 0 1-1 1A17 17 0 0 1 3 4a1 1 0 0 1 1-1h3.5a1 1 0 0 1 1 1c0 1.25.2 2.45.57 3.57a1 1 0 0 1-.25 1z"/></svg>
          07 5948 2063
        </li>
        <li>
          <svg viewBox="0 0 24 24" aria-label="Fax"><path d="M6 2h9l3 3v5H6zM3 11h18v9H3zM7 14h4v2H7z"/></svg>
          07 5948 2174
        </li>
        <li>
          <svg viewBox="0 0 24 24" aria-label="Mobile"><path d="M7 1h10a2 2 0 0 1 2 2v18a2 2 0 0 1-2 2H7a2 2 0 0 1-2-2V3a2 2 0 0 1 2-2zm0 3v15h10V4z"/></svg>
          0431 857 219
        </li>
      </ul>
    </div>
  </section>

  <section class="card card--back" aria-label="Business card back">
    <div class="brand-square"></div>
    <p class="brand-name">Walsh &amp; Brand Pty Ltd</p>
  </section>
</body>
</html>
```